Cleaning Service Company In need of Good Web presence.

The company is a cleaning service company which provides professional staff and service for cleaning. This is a project to build a site that is both solid and a strong recognition of our organization. It is supposed to show quality, cleanliness, professionalism. The use of images and art for imagery is all good just to have a site that is consistent and solid. There might be a chance to make stationary, logo and business cars if someone feels they can build a brand that is consistent. The image we are going for is clean solid and to stand out. Finally stationary should not be expensive to print.

Current logo is attached and can be used or can be made more creative.

Target Market(s)

Corporate and Government entities, that will feel that this company has a brand that sets it apart from the rest. The company is new so the modification of the logo will not be an issue if a more solid brand come out of this project. The idea is to have a clean consistent product that stands our from others in terms of website, stationary, etc

Industry/Entity Type

Cleaning Service

Contact Information for Business Card

P.O.Box 51947
Riffa
Kingdom of Bahrain

Logo Text

Harbor Lane Services

Number of Pages Required

4 page

Font styles to use
Sans Serif

Colors
abd036
cadf82
eaf2ce
9bcb3b

Requirements
Must have
• Green Color to be used in order to stick to the name. Also the creativity and boldness in an elegant manner.
Nice to have
• Arabic name of company
• هاربر لين سرفسس ذ.م.م
• if cannot be put at least make a location should be chosen
• Also could be a bit of 3D given to the logo if it could stay elegent.
Should not have
• Should not show people cleaning.

```html
<!DOCTYPE html>
<html lang="en">
<head>
<meta charset="utf-8">
<title>Harbor Lane Services W.L.L</title>
<link rel="stylesheet" href="https://fonts.googleapis.com/css2?family=Open+Sans:wght@300;400;600&family=Cairo:wght@600&display=swap">
<style>
:root{
  --green:#9bcb3b;
  --green-footer:#95c23b;
  --green-soft:#cadf82;
  --text-dark:#333333;
  --text-body:#666666;
  --nav:#444444;
  --band:#f5f5f5;
  --white:#ffffff;
  --frame:#e4e4e4;
}
*{margin:0;padding:0;box-sizing:border-box}
html,body{width:1200px;height:2479px;overflow:hidden;background:var(--white)}
body{position:relative;font-family:"Open Sans",sans-serif;color:var(--text-body)}
.abs{position:absolute}

/* header */
.brand{left:102px;top:18px;display:flex;align-items:center;gap:14px}
.brand-mark{width:40px;height:40px;border-radius:50%;background:var(--green)}
.brand-name{font-size:19px;font-weight:600;color:var(--green);line-height:1.2;width:160px}
.nav{top:58px;left:0;width:1200px;height:20px}
.nav a{position:absolute;font-size:14.5px;color:var(--nav);text-decoration:none;white-space:nowrap}
.nav a.active{color:var(--green)}

/* hero */
.hero{left:0;top:134px;width:1200px;height:511px;
  background:linear-gradient(120deg,#9fb8b0 0%,#b9cdc7 40%,#d8e2de 65%,#c9a53a 85%,#e0c24a 100%)}
.hero-title{left:0;top:290px;width:1200px;text-align:center;font-family:"Cairo",sans-serif;font-weight:600;font-size:58px;color:var(--white);direction:rtl}
.hero-arrow{top:326px;width:46px;height:46px}

/* intro */
.section-heading{font-weight:300;font-size:31px;color:var(--text-dark);line-height:1.35}
.copy{font-size:13.2px;line-height:27px;color:var(--text-body)}
.btn-outline{left:104px;top:990px;width:159px;height:40px;border:2px solid var(--green);border-radius:20px;color:var(--green);font-size:16px;font-weight:600;text-align:center;line-height:36px}
.photo-frame{border:1px solid var(--frame);background:var(--white);padding:12px}
.photo{width:100%;height:100%}

/* services */
.services{left:0;top:1098px;width:1200px;height:550px;background:var(--band)}
.services-title{left:0;top:1155px;width:1200px;text-align:center;font-weight:300;font-size:30px;color:var(--text-dark)}
.service{top:1251px;width:330px;text-align:center}
.service svg{display:block;margin:0 auto}
.service h3{margin-top:20px;font-size:19px;font-weight:600;color:var(--text-dark);letter-spacing:.3px}
.service p{margin:14px auto 0;width:310px;font-size:13.2px;line-height:23px;color:var(--text-body)}

.btn-filled{left:101px;top:2005px;width:155px;height:36px;border-radius:18px;background:var(--green);color:var(--white);font-size:14px;font-weight:600;text-align:center;line-height:36px}

/* footer */
.footer{left:0;top:2131px;width:1200px;height:348px;background:var(--green-footer)}
.footer-title{font-size:16px;font-weight:600;color:var(--white);letter-spacing:.3px}
.footer-links{list-style:none}
.footer-links li{font-size:14px;color:var(--white);height:31.5px}
.footer-note{left:772px;top:2214px;font-size:13px;color:var(--green-soft)}
.mail-input{left:775px;top:2241px;width:220px;height:39px;background:var(--white);font-size:11px;color:#b5b5b5;padding-left:18px;line-height:39px}
.mail-btn{left:995px;top:2241px;width:106px;height:39px;background:var(--green);color:var(--white);font-size:13px;font-weight:600;text-align:center;line-height:39px}
.social{top:2296px;width:40px;height:40px;border-radius:50%;background:var(--white)}
.footer-rule{left:99px;top:2402px;width:1002px;height:1px;background:rgba(255,255,255,.6)}
.copyright{left:99px;top:2429px;font-size:12.5px;color:var(--white)}
</style>
</head>
<body>

<header>
  <div class="abs brand">
    <span class="brand-mark"></span>
    <span class="brand-name">Harbor Lane Services</span>
  </div>
  <nav class="abs nav">
    <a class="active" style="left:431px">Home</a>
    <a style="left:534px">About Us</a>
    <a style="left:658px">Our Services</a>
    <a style="left:803px">Products</a>
    <a style="left:926px">Quote</a>
    <a style="left:1028px">Contact Us</a>
  </nav>
</header>

<section>
  <div class="abs hero" role="img" aria-label="Gloved hands wiping a white bathtub with a green microfibre mitt"></div>
  <h1 class="abs hero-title">هاربر لين سرفسس ذ.م.م</h1>
  <svg class="abs hero-arrow" style="left:23px" viewBox="0 0 46 46"><circle cx="23" cy="23" r="23" fill="#000" fill-opacity=".18"/><path d="M27 13 L17 23 L27 33" fill="none" stroke="#fff" stroke-width="1.5"/></svg>
  <svg class="abs hero-arrow" style="left:1131px" viewBox="0 0 46 46"><circle cx="23" cy="23" r="23" fill="#000" fill-opacity=".18"/><path d="M19 13 L29 23 L19 33" fill="none" stroke="#fff" stroke-width="1.5"/></svg>
</section>

<section>
  <h2 class="abs section-heading" style="left:99px;top:720px">Welcome to Harbor Lane Services W.L.L</h2>
  <p class="abs copy" style="left:103px;top:784px;width:545px">Lorem ipsum dolor sit amet, consectetur adipiscing elit, sed do eiusmod tempor incididunt ut labore et dolore magna aliqua. Ut enim ad minim veniam, quis nostrud exercitation ullamco laboris nisi ut aliquip ex ea commodo consequat. Duis aute irure dolor in reprehenderit in voluptate velit esse cillum dolore eu fugiat nulla pariatur. Excepteur sint occaecat cupidatat non proident, sunt in culpa qui officia deserunt mollit anim id est laborum</p>
  <div class="abs btn-outline">READ MORE</div>
  <div class="abs photo-frame" style="left:684px;top:724px;width:417px;height:307px">
    <div class="photo" role="img" aria-label="City waterfront promenade with palm trees and towers under a pale sky" style="background:linear-gradient(180deg,#e6ecef 0%,#cfd8dc 50%,#b8bfc1 75%,#dcdcd8 100%)"></div>
  </div>
</section>

<section>
  <div class="abs services"></div>
  <h2 class="abs services-title">Our Services</h2>

  <div class="abs service" style="left:83px">
    <svg width="172" height="172" viewBox="0 0 172 172"><circle cx="86" cy="86" r="86" fill="#9bcb3b"/><circle cx="86" cy="86" r="79" fill="none" stroke="#fff" stroke-width="2"/>
      <g fill="none" stroke="#fff" stroke-width="4" stroke-linejoin="round"><path d="M78 56 h18 v12 h-18 z"/><path d="M84 68 v8 h12 v-8"/><path d="M80 76 h20 l6 14 v38 h-32 v-38 z"/><path d="M96 60 h8 l4 -4"/></g>
      <g fill="#fff"><circle cx="66" cy="54" r="2.5"/><circle cx="64" cy="62" r="2.5"/><circle cx="66" cy="70" r="2.5"/></g>
      <rect x="80" y="98" width="20" height="18" fill="#fff"/></svg>
    <h3>DRY CLEANING</h3>
    <p>Sed ut perspiciatis unde omnis iste natus error sit voluptatem accusantium doloremque laudantium, totam rem aperiam, eaque ipsa quae ab illo inventore veritatis.</p>
  </div>

  <div class="abs service" style="left:433px">
    <svg width="172" height="172" viewBox="0 0 172 172"><circle cx="86" cy="86" r="86" fill="#9bcb3b"/><circle cx="86" cy="86" r="79" fill="none" stroke="#fff" stroke-width="2"/>
      <g fill="none" stroke="#fff" stroke-width="4" stroke-linecap="round"><path d="M62 100 c0 -30 30 -44 46 -30 c10 8 10 24 6 36 l10 14"/><path d="M110 122 h20"/></g>
      <ellipse cx="72" cy="114" rx="18" ry="14" fill="#fff"/><circle cx="66" cy="114" r="8" fill="#9bcb3b"/></svg>
    <h3>VACUUM CLEANING</h3>
    <p>Sed ut perspiciatis unde omnis iste natus error sit voluptatem accusantium doloremque laudantium, totam rem aperiam, eaque ipsa quae ab illo inventore veritatis.</p>
  </div>

  <div class="abs service" style="left:785px">
    <svg width="172" height="172" viewBox="0 0 172 172"><circle cx="86" cy="86" r="86" fill="#9bcb3b"/><circle cx="86" cy="86" r="79" fill="none" stroke="#fff" stroke-width="2"/>
      <g fill="#fff"><circle cx="74" cy="62" r="8"/><circle cx="90" cy="56" r="9"/><circle cx="104" cy="64" r="7"/><path d="M60 74 h52 l-6 52 h-40 z"/></g>
      <path d="M108 80 c14 0 14 20 0 20" fill="none" stroke="#fff" stroke-width="4"/>
      <rect x="74" y="88" width="24" height="22" fill="#9bcb3b"/></svg>
    <h3>OTHERS CLEANING</h3>
    <p>Sed ut perspiciatis unde omnis iste natus error sit voluptatem accusantium doloremque laudantium, totam rem aperiam, eaque ipsa quae ab illo inventore veritatis.</p>
  </div>
</section>

<section>
  <h2 class="abs section-heading" style="left:99px;top:1738px;width:540px;line-height:42px">We Serve the Govt Agencies &amp; Office in their Cleaning.</h2>
  <p class="abs copy" style="left:99px;top:1857px;width:510px">Lorem ipsum dolor sit amet, consectetur adipiscing elit, sed do eiusmod tempor incididunt ut labore et dolore magna aliqua. Ut enim ad minim veniam, quis nostrud exercitation ullamco laboris nisi ut aliquip ex ea commodo consequat.</p>
  <div class="abs btn-filled">READ MORE</div>
  <div class="abs photo-frame" style="left:661px;top:1749px;width:442px;height:294px">
    <div class="photo" role="img" aria-label="Bright living room with a white sofa and a vacuum cleaner on the floor" style="background:linear-gradient(180deg,#eef0f2 0%,#dfe2e4 55%,#cfcac2 80%,#e9e6e0 100%)"></div>
  </div>
</section>

<footer>
  <div class="abs footer"></div>
  <h4 class="abs footer-title" style="left:99px;top:2176px">USEFUL LINKS</h4>
  <ul class="abs footer-links" style="left:99px;top:2214px"><li>Home</li><li>About Us</li><li>Our Services</li><li>Products</li><li>Quote</li></ul>
  <ul class="abs footer-links" style="left:288px;top:2214px"><li>Testimonials</li><li>Contact Us</li><li>Terms &amp; Conditions</li><li>Privacy Policy</li><li>FAQS</li></ul>
  <h4 class="abs footer-title" style="left:537px;top:2176px">INFORMATION</h4>
  <ul class="abs footer-links" style="left:537px;top:2214px"><li>Specials</li><li>My Account</li><li>My Cart</li><li>Blog</li><li>Site Map</li></ul>
  <h4 class="abs footer-title" style="left:772px;top:2176px">JOIN OUR MAILING LIST</h4>
  <p class="abs footer-note">Sign up here to subscribe to our mailing list</p>
  <div class="abs mail-input">EMAIL ADDRESS</div>
  <div class="abs mail-btn">SUBSCRIBE</div>
  <span class="abs social" style="left:775px"></span>
  <span class="abs social" style="left:823px"></span>
  <span class="abs social" style="left:873px"></span>
  <span class="abs social" style="left:921px"></span>
  <div class="abs footer-rule"></div>
  <p class="abs copyright">© 2017 HARBOR LANE SERVICES W.L.L . All right reserved.&nbsp; Term of Use</p>
</footer>

</body>
</html>
```